TALMORK

The business want a professional looking business card. We have a scetch we will add but want the extra upgrade, and would like more suggestions for variations of our business cards.

```html
<!DOCTYPE html>
<html lang="en">
<head>
<meta charset="utf-8">
<title>TALMORK – Business Card</title>
<link href="https://fonts.googleapis.com/css2?family=Playfair+Display:wght@500&family=Poppins:wght@400;500&display=swap" rel="stylesheet">
<style>
  :root {
    --backdrop: #2b2b2d;
    --card: #1f1f20;
    --gold: #d9b24a;
    --gold-soft: #e6c466;
  }
  html, body {
    margin: 0;
    padding: 0;
    width: 1200px;
    height: 900px;
    overflow: hidden;
    background: var(--backdrop);
  }
  .canvas {
    position: relative;
    width: 1200px;
    height: 900px;
    display: flex;
    flex-direction: column;
    align-items: center;
    justify-content: center;
    gap: 56px;
  }
  .card {
    position: relative;
    width: 600px;
    height: 343px;
    background: var(--card);
    border-radius: 22px;
    box-shadow: 0 10px 30px rgba(0,0,0,0.45);
    overflow: hidden;
  }

  /* Front */
  .card-front {
    display: flex;
    flex-direction: column;
    align-items: center;
    justify-content: center;
    gap: 26px;
  }
  .brand-dot {
    width: 96px;
    height: 96px;
    border-radius: 50%;
    background: var(--gold);
  }
  .brand-name {
    font-family: "Playfair Display", serif;
    font-weight: 500;
    color: var(--gold);
    letter-spacing: 0.32em;
    margin: 0;
  }
  .card-front .brand-name {
    font-size: 50px;
    padding-left: 0.32em;
  }

  /* Back */
  .card-back .brand-row {
    position: absolute;
    top: 42px;
    left: 48px;
    display: flex;
    align-items: center;
    gap: 22px;
  }
  .card-back .brand-dot {
    width: 58px;
    height: 58px;
  }
  .brand-block {
    display: flex;
    flex-direction: column;
    align-items: center;
  }
  .card-back .brand-name {
    font-size: 36px;
    padding-left: 0.32em;
  }
  .brand-since {
    font-family: "Poppins", sans-serif;
    font-size: 11px;
    letter-spacing: 0.4em;
    color: var(--gold);
    margin-top: 2px;
  }
  .person {
    position: absolute;
    left: 48px;
    top: 168px;
    color: var(--gold);
  }
  .person-name {
    font-family: "Playfair Display", serif;
    font-weight: 500;
    font-size: 25px;
    margin: 0 0 4px;
  }
  .person-role,
  .person-legal {
    font-family: "Poppins", sans-serif;
    font-size: 13px;
    margin: 0;
    line-height: 1.45;
  }
  .contact-list {
    list-style: none;
    margin: 14px 0 0;
    padding: 0;
    font-family: "Poppins", sans-serif;
    font-size: 13px;
  }
  .contact-list li {
    display: flex;
    align-items: center;
    gap: 10px;
    line-height: 1.75;
  }
  .contact-icon {
    width: 13px;
    height: 13px;
    fill: var(--gold);
    flex: none;
  }
</style>
</head>
<body>
<main class="canvas">

  <section class="card card-front" aria-label="Business card front">
    <span class="brand-dot" aria-hidden="true"></span>
    <h1 class="brand-name">TALMORK</h1>
  </section>

  <section class="card card-back" aria-label="Business card back">
    <div class="brand-row">
      <span class="brand-dot" aria-hidden="true"></span>
      <div class="brand-block">
        <h2 class="brand-name">TALMORK</h2>
        <span class="brand-since">SINCE 2026</span>
      </div>
    </div>

    <div class="person">
      <p class="person-name">Talmork Vestby</p>
      <p class="person-role">CEO &amp; Founder</p>
      <p class="person-legal">Arne Holm Vestby</p>

      <ul class="contact-list">
        <li>
          <svg class="contact-icon" viewBox="0 0 16 16" aria-hidden="true">
            <path d="M3 1h3l1.5 3.5-2 1.3a9 9 0 0 0 4.7 4.7l1.3-2L15 10v3a2 2 0 0 1-2 2A12 12 0 0 1 1 3a2 2 0 0 1 2-2z"/>
          </svg>
          004791234567
        </li>
        <li>
          <svg class="contact-icon" viewBox="0 0 16 16" aria-hidden="true">
            <path d="M1 3h14v10H1z M1.5 3.5 8 9l6.5-5.5" stroke="#1f1f20" stroke-width="1.2"/>
          </svg>
          talmork.llc@mailbox.com
        </li>
        <li>
          <svg class="contact-icon" viewBox="0 0 16 16" aria-hidden="true">
            <circle cx="8" cy="8" r="7"/>
            <path d="M1 8h14M8 1c-3 3.5-3 10.5 0 14M8 1c3 3.5 3 10.5 0 14" fill="none" stroke="#1f1f20" stroke-width="1"/>
          </svg>
          www.talmork.llc
        </li>
      </ul>
    </div>
  </section>

</main>
</body>
</html>
```